Redesign current business card for food company

i would like to redesign my business card. our company is food company, our product range from chips, juices, milk and etc (mostly dried food stuff).
I want o keep same logo but , the rest is open to new design.
you can check at our website about our company www.orvelpantry.com

Target Market(s)

most of food company

Industry/Entity Type

Business

Contact Information for Business Card

I want to keep more to blue color...

Colors
3176b5
abd036

Requirements
Must have
• our old logo
Nice to have
• we do not mind to have nice material on bus card in order to accomplish nice design. for example: using spot uv, embossed and etc.

```html
<!DOCTYPE html>
<html lang="en">
<head>
<meta charset="utf-8">
<title>Orvel Business Card</title>
<link rel="stylesheet" href="https://fonts.googleapis.com/css2?family=Source+Sans+3:wght@400;600;700&display=swap">
<style>
  :root {
    --stage: #000000;
    --card: #ffffff;
    --blue: #3176b5;
    --blue-deep: #1f5a94;
    --blue-light: #5a9ad3;
    --green: #abd036;
    --text-light: #ffffff;
    --ink: #1c3550;
    --produce-a: #f0d27a;
    --produce-b: #b7d36a;
    --produce-c: #e9e4dc;
  }
  * { margin: 0; padding: 0; box-sizing: border-box; }
  html, body {
    width: 1200px; height: 900px; overflow: hidden;
    background: var(--stage);
    font-family: "Source Sans 3", Arial, sans-serif;
  }
  .card {
    position: absolute; top: 306px;
    width: 439px; height: 271px;
    border-radius: 10px; overflow: hidden;
    background: var(--card);
  }
  .card--front { left: 149px; }
  .card--back { left: 608px; display: flex; align-items: center; justify-content: center; }
  .front-art { position: absolute; inset: 0; }
  .contact {
    position: absolute; left: 30px; top: 38px;
    color: var(--text-light);
  }
  .contact__name { font-size: 15.5px; font-weight: 700; line-height: 19px; }
  .contact__role { font-size: 12px; line-height: 15px; }
  .contact__company { font-size: 13.5px; font-weight: 600; margin-top: 8px; line-height: 17px; }
  .contact__address { font-size: 12px; line-height: 19px; margin-top: 1px; }
  .contact__list { list-style: none; margin-top: 5px; }
  .contact__item { display: flex; align-items: center; font-size: 12px; line-height: 18.5px; }
  .contact__icon { width: 9px; height: 9px; margin-right: 10px; margin-left: 1px; fill: var(--text-light); flex: none; }
  .brand__name {
    font-size: 84px; font-weight: 700; letter-spacing: -1px;
    color: var(--ink); line-height: 1;
  }
</style>
</head>
<body>
  <section class="card card--front">
    <svg class="front-art" viewBox="0 0 439 271" width="439" height="271">
      <defs>
        <linearGradient id="leafFill" x1="0" y1="1" x2="1" y2="0">
          <stop offset="0" stop-color="var(--blue-deep)"/>
          <stop offset="0.55" stop-color="var(--blue)"/>
          <stop offset="1" stop-color="var(--blue-light)"/>
        </linearGradient>
        <linearGradient id="produceFill" x1="0" y1="0" x2="0" y2="1">
          <stop offset="0" stop-color="var(--produce-a)"/>
          <stop offset="0.5" stop-color="var(--produce-b)"/>
          <stop offset="1" stop-color="var(--produce-c)"/>
        </linearGradient>
      </defs>
      <path class="front-art__base" d="M0 0 H376 C340 120 230 230 100 271 H0 Z" fill="var(--blue)"/>
      <path class="front-art__leaf" d="M100 271 C150 140 250 40 376 0 C340 120 230 230 100 271 Z" fill="url(#leafFill)"/>
      <path class="front-art__edge" d="M100 271 C230 230 340 120 376 0 L380 0 C346 124 236 236 108 271 Z" fill="var(--green)"/>
      <g role="img" aria-label="Photo of pineapple, cheese, crackers, grapes, apple, lemon and a milk splash">
        <path d="M384 0 H439 V271 H300 C330 230 358 172 370 112 C377 72 381 34 384 0 Z" fill="url(#produceFill)" opacity="0.85"/>
      </g>
    </svg>
    <div class="contact">
      <p class="contact__name">Marcus Dellaventi</p>
      <p class="contact__role">President</p>
      <p class="contact__company">Orvel Enterprises Corp.</p>
      <p class="contact__address">2417 W 5th St.Corvale<br>CA 90412</p>
      <ul class="contact__list">
        <li class="contact__item">
          <svg class="contact__icon" viewBox="0 0 10 10"><path d="M2 0.5 L3.5 2.6 L2.6 3.6 C3.2 5 4.8 6.6 6.4 7.4 L7.4 6.5 L9.5 8 L8.6 9.5 C4.5 9.3 0.7 5.5 0.5 1.4 Z"/></svg>
          909 555 0142
        </li>
        <li class="contact__item">
          <svg class="contact__icon" viewBox="0 0 10 10"><path d="M2.5 0.5 H7 V3 H9.5 V9.5 H0.5 V3 H2.5 Z M3.5 1.5 V3 H6 V1.5 Z"/></svg>
          909 555 0187
        </li>
        <li class="contact__item">
          <svg class="contact__icon" viewBox="0 0 10 10"><path d="M2 0 H8 V10 H2 Z M3 1.2 V7.6 H7 V1.2 Z"/></svg>
          626 555 0193
        </li>
        <li class="contact__item">
          <svg class="contact__icon" viewBox="0 0 10 10"><path d="M0.5 2 H9.5 V8.5 H0.5 Z M1.3 2.8 L5 5.6 L8.7 2.8 Z" fill-rule="evenodd"/></svg>
          Marcus@orvelpantry.com
        </li>
        <li class="contact__item">
          <svg class="contact__icon" viewBox="0 0 10 10"><circle cx="5" cy="5" r="4.5"/></svg>
          www.orvelpantry.com
        </li>
      </ul>
    </div>
  </section>

  <section class="card card--back">
    <span class="brand__name">orvel</span>
  </section>
</body>
</html>
```